RWT Fittings Ltd Business Cards

We need a business card with our business logo. We provide window and door installations on high-rises in west coast British Colombia, Canada.

I would like my business information and details on one side of the card, and the other side the company name with logo

Target Market(s)

General Contractors

Industry/Entity Type

Construction

Contact Information for Business Card

one side i want my company name and logo in the dark theme logo that i provided

Requirements
Must have
• Marco Peltieri, 16045518293, RWTFittings@mailbox-demo.com, 1407-5194 Linden Row Burnaby BC, V5H 2K9, Owner & Manager

```html
<!DOCTYPE html>
<html lang="en">
<head>
<meta charset="utf-8">
<title>RWT Fittings Ltd – Business Cards</title>
<link href="https://fonts.googleapis.com/css2?family=Roboto:wght@400;700;900&display=swap" rel="stylesheet">
<style>
  :root{
    --stage:#232323;
    --card-back:#1e1f23;
    --card-front-dark:#1b1a19;
    --card-front-mid:#3a3735;
    --edge-blue:#29a8e0;
    --accent-blue:#2ab0e8;
    --name-grey:#a9a9ab;
    --text-light:#f2f2f2;
    --emboss:#151619;
    --facet:#26282d;
  }
  *{margin:0;padding:0;box-sizing:border-box}
  html,body{width:1200px;height:780px;overflow:hidden;background:var(--stage)}
  body{position:relative;font-family:"Roboto",Arial,sans-serif}

  .card{
    position:absolute;width:580px;height:332px;border-radius:22px;overflow:hidden;
    border-bottom:6px solid var(--edge-blue);border-left:3px solid var(--edge-blue);
    box-shadow:0 18px 40px rgba(0,0,0,.55);
  }

  /* Front side */
  .card--front{left:70px;top:60px}
  .front-photo{
    position:absolute;inset:0;
    background:radial-gradient(ellipse at 60% 35%,var(--card-front-mid) 0%,#2a2827 45%,var(--card-front-dark) 100%);
  }
  .brand{
    position:absolute;left:0;right:0;top:50%;transform:translateY(-50%);
    display:flex;align-items:center;justify-content:center;gap:16px;
  }
  .brand-mark{width:34px;height:34px;background:var(--accent-blue)}
  .brand-name{font-weight:900;font-size:46px;color:var(--accent-blue);letter-spacing:1px}

  /* Back side */
  .card--back{left:550px;top:400px;background:var(--card-back)}
  .facet{position:absolute;background:var(--facet)}
  .facet--a{right:0;top:0;width:220px;height:100%;clip-path:polygon(60% 0,100% 0,100% 100%,0 100%)}
  .facet--b{right:150px;top:120px;width:120px;height:100px;opacity:.7}

  .watermark-name{
    position:absolute;left:26px;bottom:28px;
    font-weight:900;font-size:34px;color:var(--emboss);line-height:1.05;
  }

  .contact{position:absolute;right:30px;top:34px;text-align:right;color:var(--text-light)}
  .name-row{display:flex;align-items:center;justify-content:flex-end;gap:12px}
  .person-name{font-weight:700;font-size:30px;line-height:1}
  .person-name .first{color:var(--accent-blue)}
  .person-name .last{color:var(--name-grey)}
  .name-tab{width:14px;height:46px;background:var(--accent-blue)}
  .role{font-weight:700;font-size:13px;margin:4px 26px 0 0}

  .address{margin-top:36px;font-size:14px;line-height:1.35}
  .lines{margin-top:22px;font-size:14px;line-height:1.6}
  .line{display:flex;align-items:center;justify-content:flex-end;gap:8px}
  .line svg{width:14px;height:14px;flex:none}
</style>
</head>
<body>

<section class="card card--front" aria-label="Business card front">
  <div class="front-photo" role="img" aria-label="Dim photograph of a modern interior with a plant, softly out of focus"></div>
  <div class="brand">
    <span class="brand-mark"></span>
    <span class="brand-name">RWT Fittings Ltd</span>
  </div>
</section>

<section class="card card--back" aria-label="Business card back">
  <div class="facet facet--a"></div>
  <div class="facet facet--b"></div>

  <div class="watermark-name">RWT<br>Fittings Ltd</div>

  <div class="contact">
    <div class="name-row">
      <div class="person-name"><span class="first">Marco</span> <span class="last">Peltieri</span></div>
      <span class="name-tab"></span>
    </div>
    <div class="role">Owner &amp; Manager</div>

    <div class="address">1407-5194 Linden Row<br>Burnaby BC, V5H 2K9</div>

    <div class="lines">
      <div class="line">1604 551 8293
        <svg viewBox="0 0 24 24" aria-hidden="true"><path fill="var(--accent-blue)" d="M6.6 10.8a15 15 0 0 0 6.6 6.6l2.2-2.2c.3-.3.7-.4 1-.2 1.1.4 2.3.6 3.6.6.6 0 1 .4 1 1V20c0 .6-.4 1-1 1A17 17 0 0 1 3 4c0-.6.4-1 1-1h3.5c.6 0 1 .4 1 1 0 1.3.2 2.5.6 3.6.1.3 0 .7-.2 1z"/></svg>
      </div>
      <div class="line">RWTFittings@mailbox-demo.com
        <svg viewBox="0 0 24 24" aria-hidden="true"><rect x="2" y="5" width="20" height="14" rx="1.5" fill="var(--accent-blue)"/><path d="M3 6l9 7 9-7" fill="none" stroke="var(--card-back)" stroke-width="1.8"/></svg>
      </div>
    </div>
  </div>
</section>

</body>
</html>
```